Redesign of business card for Cedar Ridge Mechanical

We are looking for a new design for our business cards for Cedar Ridge Mechanical. We are a plumbing & HVAC construction company, operating on the West Coast of Canada and USA. Logo attached.
Industry/Entity Type
Construction - Plumbing & HVAC
Contact Information for Business Card
Name, address, phone numbers, email, website address
Look and feel
Each slider illustrates characteristics of the customer's brand and the style your logo design should communicate.

```html
<!DOCTYPE html>
<html lang="en">
<head>
<meta charset="utf-8">
<title>Cedar Ridge Mechanical – Business Card</title>
<link href="https://fonts.googleapis.com/css2?family=Open+Sans:wght@400;600;700&display=swap" rel="stylesheet">
<style>
  :root {
    --backdrop: #d2d2d2;
    --ink: #000000;
    --paper: #ffffff;
    --accent-grey: #8a8c8d;
  }
  * { margin: 0; padding: 0; box-sizing: border-box; }
  html, body { width: 1200px; height: 896px; overflow: hidden; }
  body {
    background: var(--backdrop);
    font-family: "Open Sans", Arial, sans-serif;
    position: relative;
  }
  .card {
    position: absolute;
    left: 334px;
    width: 527px;
    height: 301px;
    border-radius: 24px;
    background: var(--paper);
    overflow: hidden;
  }
  .card--front { top: 126px; }
  .card--back { top: 474px; }

  .wordmark {
    display: flex;
    align-items: center;
    gap: 14px;
    color: var(--ink);
    font-weight: 700;
    text-transform: uppercase;
    line-height: 1.1;
  }
  .wordmark__square {
    background: var(--ink);
    flex: none;
  }
  .card--front .wordmark {
    position: absolute;
    left: 0; right: 0; top: 0; bottom: 0;
    justify-content: center;
    font-size: 30px;
    letter-spacing: 1px;
  }
  .card--front .wordmark__square { width: 34px; height: 34px; }

  .back-art { position: absolute; inset: 0; }
  .card--back .wordmark {
    position: absolute;
    left: 268px; right: 20px; top: 0; bottom: 0;
    justify-content: center;
    font-size: 21px;
    letter-spacing: 0.5px;
  }
  .card--back .wordmark__square { width: 24px; height: 24px; }

  .contact {
    position: absolute;
    left: 24px;
    top: 54px;
    color: var(--paper);
  }
  .contact__name { font-size: 18px; font-weight: 700; letter-spacing: 0.2px; }
  .contact__role { font-size: 13.5px; margin-top: -2px; padding-left: 2px; }
  .contact__rule { width: 49px; height: 1.5px; background: var(--paper); margin-top: 4px; }
  .contact__address { font-size: 14px; line-height: 19px; margin-top: 25px; }
  .contact__rule--mid { margin-top: 17px; }
  .contact__list { list-style: none; margin-top: 16px; font-size: 14px; line-height: 19px; }
  .contact__list li { display: flex; align-items: center; gap: 6px; }
  .contact__list svg { width: 12px; height: 12px; flex: none; }
</style>
</head>
<body>

<section class="card card--front" aria-label="Card front">
  <div class="wordmark">
    <span class="wordmark__square"></span>
    <span>Cedar Ridge<br>Mechanical</span>
  </div>
</section>

<section class="card card--back" aria-label="Card back">
  <svg class="back-art" viewBox="0 0 527 301" width="527" height="301" aria-hidden="true">
    <path d="M0 0 H292 C236 60 212 200 266 301 H0 Z" fill="var(--ink)"/>
    <path d="M298 2 C246 70 232 205 301 301 H278 C222 210 240 70 298 2 Z" fill="var(--accent-grey)"/>
  </svg>

  <div class="contact">
    <p class="contact__name">ETHAN WALSH</p>
    <p class="contact__role">Managing Director</p>
    <div class="contact__rule"></div>
    <p class="contact__address">Your address, City<br>State, Zip 1234</p>
    <div class="contact__rule contact__rule--mid"></div>
    <ul class="contact__list">
      <li>
        <svg viewBox="0 0 12 12"><path d="M2.5 1 L4.5 1 L5.2 3.5 L4 4.5 C4.6 6 6 7.4 7.5 8 L8.5 6.8 L11 7.5 L11 9.5 C11 10.3 10.3 11 9.5 11 C5 11 1 7 1 2.5 C1 1.7 1.7 1 2.5 1 Z" fill="#fff"/></svg>
        123 456 789
      </li>
      <li>
        <svg viewBox="0 0 12 12"><rect x="1" y="3" width="10" height="7" fill="none" stroke="#fff" stroke-width="1.2"/><path d="M1 3 L6 7 L11 3" fill="none" stroke="#fff" stroke-width="1.2"/></svg>
        info@yourmail.com
      </li>
      <li>
        <svg viewBox="0 0 12 12"><circle cx="6" cy="6" r="5" fill="none" stroke="#fff" stroke-width="1.2"/><ellipse cx="6" cy="6" rx="2" ry="5" fill="none" stroke="#fff" stroke-width="1"/><path d="M1 6 H11" stroke="#fff" stroke-width="1"/></svg>
        www.yourwebsite.com
      </li>
    </ul>
  </div>

  <div class="wordmark">
    <span class="wordmark__square"></span>
    <span>Cedar Ridge<br>Mechanical</span>
  </div>
</section>

</body>
</html>
```